Korvalith Brochure Design - IT Services - Modern Design - Services List

Hi,

We are looking for a modern IT Services brochure design of between 4 - 6 pages, it must be based on a blue and white colour theme with some nice technical imagery. It would need a section about why Korvalith and a contact section at the end.

Here is some info that could be included

Target Market(s)

Medium to Large Businesses

Industry/Entity Type

Information Technology

Colors
0054AA
0677BA
7BADD7
CADEEF
E8F1F8

Requirements
Must have
• Striking technical imagery
Nice to have
• Nice Icons to list the different services sections

```html
<!DOCTYPE html>
<html lang="en">
<head>
<meta charset="utf-8">
<title>Korvalith – IT Services Brochure</title>
<link href="https://fonts.googleapis.com/css2?family=Poppins:wght@300;400;500;600;700;800&display=swap" rel="stylesheet">
<style>
:root{
  --stage:#646464;
  --white:#ffffff;
  --paper:#f4f6f8;
  --blue:#1b93d6;
  --blue-deep:#0054aa;
  --blue-mid:#0677ba;
  --blue-soft:#7badd7;
  --blue-pale:#cadeef;
  --blue-mist:#e8f1f8;
  --ink:#2b2f36;
  --ink-soft:#4a4f57;
  --rule:#7d8288;
}
*{box-sizing:border-box;margin:0;padding:0}
html,body{width:1200px;height:2166px;overflow:hidden}
body{background:var(--stage);font-family:"Poppins",sans-serif;color:var(--ink);position:relative}
.page{position:absolute;width:496px;overflow:hidden}
.page--light{background:linear-gradient(160deg,var(--paper) 0%,var(--white) 45%,var(--paper) 100%)}

/* cover */
.cover{left:90px;top:73px;height:636px;background:var(--white)}
.cover__name{position:absolute;top:34px;left:0;right:0;text-align:center;font-weight:700;font-size:36px;color:var(--blue);letter-spacing:1px;line-height:44px}
.cover__photo{position:absolute;top:113px;left:0;width:496px;height:350px;background:linear-gradient(110deg,#c9b39e 0%,#e9e3dd 35%,#f3f1ee 60%,#dfe7ee 100%)}
.cover__band{position:absolute;top:463px;left:0;width:496px;height:173px;background:linear-gradient(135deg,var(--blue-mid) 0%,var(--blue) 60%,#1aa2e2 100%);text-align:center;color:var(--white)}
.cover__rule{width:24px;height:2px;background:var(--white);margin:36px auto 14px}
.cover__headline{font-weight:800;font-size:20px;line-height:25px}
.cover__web{margin-top:26px;font-size:11px;letter-spacing:6px;font-weight:500;display:flex;align-items:center;justify-content:center;gap:4px}

/* about */
.about{left:616px;top:71px;height:642px;background:var(--white)}
.about__frame{position:absolute;left:18px;top:17px;width:460px;height:606px;background:linear-gradient(180deg,#5f8aa6 0%,#3f6a86 35%,#1d3a52 70%,#0f2236 100%)}
.about__title{position:absolute;left:45px;top:40px;font-weight:800;font-size:20px;color:var(--white)}
.about__text{position:absolute;left:45px;top:72px;width:410px;font-size:8.6px;line-height:11.7px;color:var(--white);font-weight:300}

/* service pages */
.services-a{left:88px;top:761px;height:641px}
.services-b{left:616px;top:762px;height:641px}
.page__title{position:absolute;left:43px;top:30px;font-weight:800;font-size:25px;color:var(--blue);line-height:1}
.page__rule{position:absolute;left:44px;top:69px;width:57px;height:2px;background:var(--rule)}
.service{position:absolute;left:40px;width:440px}
.service__head{display:flex;align-items:center;gap:9px}
.icon-ring{width:48px;height:48px;border:1.5px solid var(--blue);border-radius:50%;display:flex;align-items:center;justify-content:center;flex:none;background:var(--white)}
.service__name{font-weight:800;font-size:13px;color:var(--blue)}
.service__intro{margin:10px 0 0 4px;font-size:10px;line-height:13.5px;color:var(--ink-soft);font-weight:300}
.offer-grid{display:grid;grid-template-columns:207px 207px;column-gap:0;row-gap:8px;margin:10px 0 0 4px}
.offer{position:relative;padding-left:17px;font-size:8.6px;line-height:11.6px;color:var(--ink-soft);font-weight:300}
.offer::before{content:"";position:absolute;left:3px;top:3px;width:6px;height:6px;border:1.2px solid var(--blue);transform:rotate(45deg)}
.offer strong{display:block;font-weight:600;color:var(--ink)}
.page__foot{position:absolute;left:0;bottom:0;width:100%;height:124px}
.foot--cloud{background:linear-gradient(100deg,#23415e 0%,#1f6aa0 35%,#1684c8 65%,#0b8ad2 100%)}
.foot--lock{background:linear-gradient(100deg,#0e1f33 0%,#1d5c8c 35%,#2a8ccc 55%,#0f78c0 100%)}
.foot--chip{background:linear-gradient(100deg,#0a1a3a 0%,#23579a 35%,#4fa3de 50%,#0f7ac4 100%)}
.page__num{position:absolute;right:22px;bottom:19px;width:27px;height:27px;border:1.3px solid var(--white);border-radius:50%;color:var(--white);font-size:10px;font-weight:600;display:flex;align-items:center;justify-content:center}

/* why choose */
.why{left:89px;top:1454px;height:642px}
.reason{position:absolute;width:200px}
.reason__head{display:flex;align-items:center;gap:9px}
.reason__name{font-weight:800;font-size:12.5px;line-height:15px;color:var(--blue)}
.reason__text{margin-top:10px;font-size:10.2px;line-height:13.6px;color:var(--ink-soft);font-weight:300}

/* contact */
.contact{left:615px;top:1454px;height:643px;background:linear-gradient(160deg,#0d8fd3 0%,var(--blue) 50%,#0f8dd0 100%);color:var(--white);text-align:center}
.contact__title{position:absolute;top:185px;left:0;right:0;font-weight:600;font-size:31px;line-height:1}
.contact__rule{position:absolute;top:239px;left:224px;width:50px;height:2px;background:var(--white)}
.contact__lead{position:absolute;top:260px;left:50px;right:50px;font-size:11.2px;line-height:14.6px;font-weight:300}
.contact__label{position:absolute;left:0;right:0;font-size:13px;font-weight:600;letter-spacing:4.5px}
.contact__address{position:absolute;top:371px;left:0;right:0;font-size:11.3px;font-weight:300}
.contact__row{position:absolute;top:391px;left:0;right:0;display:flex;justify-content:center;gap:14px;font-size:11px;font-weight:300}
.contact__item{display:flex;align-items:center;gap:5px}
.contact__icon{width:26px;height:26px;border:1.2px solid var(--white);border-radius:50%;display:flex;align-items:center;justify-content:center}
.contact__follow{position:absolute;top:477px;left:0;right:0;font-size:11.3px;font-weight:300}
.social{position:absolute;top:501px;left:0;right:0;display:flex;justify-content:center;gap:6px}
.social__dot{width:22px;height:22px;border-radius:50%;background:var(--white)}
</style>
</head>
<body>

<section class="page cover">
  <div class="cover__name">KORVALITH</div>
  <div class="cover__photo" role="img" aria-label="Photo of smiling support team members wearing headsets at their desks"></div>
  <div class="cover__band">
    <div class="cover__rule"></div>
    <div class="cover__headline">EMPOWERING YOUR BUSINESS<br>WITH CUTTING-EDGE IT SOLUTIONS</div>
    <div class="cover__web">
      <svg width="13" height="13" viewBox="0 0 24 24" fill="none" stroke="#fff" stroke-width="1.6"><circle cx="12" cy="12" r="10"/><ellipse cx="12" cy="12" rx="4.5" ry="10"/><path d="M2 12h20M4 7h16M4 17h16"/></svg>
      WWW.KORVALITH.CO.UK
    </div>
  </div>
</section>

<section class="page about">
  <div class="about__frame" role="img" aria-label="Night city skyline with glowing connected network icons for web, mobile and finance"></div>
  <h2 class="about__title">ABOUT KORVALITH</h2>
  <p class="about__text">At Korvalith, we are dedicated to providing top-tier IT services that drive efficiency, innovation, and growth for your business. With a commitment to excellence and a team of highly skilled professionals, we offer a comprehensive suite of solutions tailored to meet the unique needs of our clients.</p>
</section>

<section class="page page--light services-a">
  <h2 class="page__title">OUR SERVICES</h2>
  <div class="page__rule"></div>

  <div class="service" style="top:92px">
    <div class="service__head">
      <div class="icon-ring"><svg width="26" height="26" viewBox="0 0 24 24" fill="none" stroke="var(--blue)" stroke-width="1.4"><rect x="3" y="4" width="18" height="12" rx="1"/><path d="M9 20h6M12 16v4"/><circle cx="12" cy="10" r="2.5"/></svg></div>
      <h3 class="service__name">MANAGED IT SERVICES</h3>
    </div>
    <p class="service__intro">Our Managed IT Services provide proactive monitoring and management of your IT infrastructure, ensuring maximum uptime and reliability. We offer:</p>
    <div class="offer-grid">
      <div class="offer"><strong>24/7 Network Monitoring:</strong>Continuous monitoring to detect and resolve issues before they impact your business.</div>
      <div class="offer"><strong>Patch Management:</strong>Regular updates and patches to keep your systems secure and up-to-date.</div>
      <div class="offer"><strong>Helpdesk Support:</strong>Responsive and knowledgeable support team available round the clock.</div>
      <div class="offer" style="margin-top:-12px"><strong>IT Asset Management:</strong>Comprehensive tracking and management of your IT assets</div>
    </div>
  </div>

  <div class="service" style="top:304px">
    <div class="service__head">
      <div class="icon-ring"><svg width="26" height="26" viewBox="0 0 24 24" fill="none" stroke="var(--blue)" stroke-width="1.4"><path d="M7 17a4 4 0 0 1 0-8 5 5 0 0 1 9.6-1A4 4 0 0 1 17 17z"/><path d="M12 12v5M10 15l2 2 2-2"/></svg></div>
      <h3 class="service__name">CLOUD SOLUTIONS</h3>
    </div>
    <p class="service__intro">Embrace the power of the cloud with our scalable and secure cloud solutions.<br>Our offerings include:</p>
    <div class="offer-grid">
      <div class="offer"><strong>Cloud Migration:</strong>Seamless transition of your applications and data to the cloud.</div>
      <div class="offer"><strong>Backup and Disaster Recovery:</strong>Robust backup and recovery solutions to ensure business continuity.</div>
      <div class="offer"><strong>Cloud Hosting:</strong>Reliable and scalable hosting solutions to meet your growing needs.</div>
      <div class="offer"><strong>Software as a Service (SaaS):</strong>Access to the latest software applications without the hassle of maintenance.</div>
    </div>
  </div>

  <div class="page__foot foot--cloud" role="img" aria-label="Engineer holding a laptop with floating cloud computing icons"></div>
  <div class="page__num">02</div>
</section>

<section class="page page--light services-b">
  <h2 class="page__title">OUR SERVICES</h2>
  <div class="page__rule"></div>

  <div class="service" style="top:92px">
    <div class="service__head">
      <div class="icon-ring"><svg width="26" height="26" viewBox="0 0 24 24" fill="none" stroke="var(--blue)" stroke-width="1.4"><rect x="7" y="11" width="10" height="8" rx="1"/><path d="M9 11V8a3 3 0 0 1 6 0v3"/><path d="M3 8h2M19 8h2M3 16h2M19 16h2"/></svg></div>
      <h3 class="service__name">CYBER SECURITY</h3>
    </div>
    <p class="service__intro">Protect your business from evolving threats with our comprehensive cybersecurity<br>services. We offer:</p>
    <div class="offer-grid">
      <div class="offer"><strong>Threat Detection and Response:</strong>Advanced threat monitoring and response to safeguard your data.</div>
      <div class="offer"><strong>Endpoint Protection:</strong>Robust security solutions for all your devices.</div>
      <div class="offer"><strong>Security Audits and Assessments:</strong>Thorough evaluations to identify and mitigate vulnerabilities.</div>
      <div class="offer"><strong>Compliance and Regulatory Services:</strong>Ensure adherence to industry standards and regulations.</div>
    </div>
  </div>

  <div class="service" style="top:290px">
    <div class="service__head">
      <div class="icon-ring"><svg width="26" height="26" viewBox="0 0 24 24" fill="none" stroke="var(--blue)" stroke-width="1.4"><path d="M4 5h16v10H10l-4 4v-4H4z"/><circle cx="9" cy="10" r=".8"/><circle cx="12" cy="10" r=".8"/><circle cx="15" cy="10" r=".8"/></svg></div>
      <h3 class="service__name">IT CONSULTING</h3>
    </div>
    <p class="service__intro">Leverage our expertise to drive your IT strategy and achieve your business goals.<br>Our consulting services include:</p>
    <div class="offer-grid">
      <div class="offer"><strong>IT Strategy and Planning:</strong>Strategic guidance to align your IT initiatives with your business objectives.</div>
      <div class="offer"><strong>Project Management:</strong>Expert management of IT projects from inception to completion.</div>
      <div class="offer"><strong>Technology Assessments:</strong>In-depth evaluations to optimize your IT infrastructure.</div>
      <div class="offer"><strong>Business Continuity Planning:</strong>Strategies to ensure your business remains operational during disruptions.</div>
    </div>
  </div>

  <div class="page__foot foot--lock" role="img" aria-label="Glowing digital shield and padlock over a circuit board"></div>
  <div class="page__num">03</div>
</section>

<section class="page page--light why">
  <h2 class="page__title" style="left:42px">WHY CHOOSE KORVALITH?</h2>
  <div class="page__rule" style="left:43px"></div>

  <div class="reason" style="left:41px;top:98px">
    <div class="reason__head">
      <div class="icon-ring"><svg width="26" height="26" viewBox="0 0 24 24" fill="none" stroke="var(--blue)" stroke-width="1.4"><circle cx="12" cy="12" r="3"/><path d="M12 3v3M12 18v3M3 12h3M18 12h3M5.6 5.6l2.1 2.1M16.3 16.3l2.1 2.1M5.6 18.4l2.1-2.1M16.3 7.7l2.1-2.1"/></svg></div>
      <h3 class="reason__name">EXPERTISE<br>AND EXPERIENCE</h3>
    </div>
    <p class="reason__text">With years of experience in the IT industry, our team possesses the knowledge and skills to tackle any challenge. We stay abreast of the latest technological advancements to provide you with cutting-edge solutions.</p>
  </div>

  <div class="reason" style="left:262px;top:98px;width:210px">
    <div class="reason__head">
      <div class="icon-ring"><svg width="26" height="26" viewBox="0 0 24 24" fill="none" stroke="var(--blue)" stroke-width="1.4"><circle cx="8" cy="8" r="2.5"/><circle cx="16" cy="8" r="2.5"/><path d="M3 17c0-3 2.2-5 5-5s5 2 5 5M11 17c0-3 2.2-5 5-5s5 2 5 5"/></svg></div>
      <h3 class="reason__name">CUSTOMER-CENTRIC<br>APPROACH</h3>
    </div>
    <p class="reason__text">We prioritize our clients' needs and work closely with them to deliver customized solutions that drive success. Our client-centric approach ensures that we are always aligned with your business goals.</p>
  </div>

  <div class="reason" style="left:41px;top:271px">
    <div class="reason__head">
      <div class="icon-ring"><svg width="26" height="26" viewBox="0 0 24 24" fill="none" stroke="var(--blue)" stroke-width="1.4"><path d="M4 14l5-5 3 2 3-3 5 5-6 6z"/><path d="M9 14l3 3"/></svg></div>
      <h3 class="reason__name">PROACTIVE<br>SUPPORT</h3>
    </div>
    <p class="reason__text">Our proactive support model ensures that potential issues are identified and resolved before they can impact your operations. We are committed to maintaining the highest levels of service availability and performance.</p>
  </div>

  <div class="reason" style="left:262px;top:271px;width:210px">
    <div class="reason__head">
      <div class="icon-ring"><svg width="26" height="26" viewBox="0 0 24 24" fill="none" stroke="var(--blue)" stroke-width="1.4"><path d="M5 5h6v2a2 2 0 0 0 4 0V5h4v14H5z"/></svg></div>
      <h3 class="reason__name">COMPREHENSIVE<br>SOLUTIONS</h3>
    </div>
    <p class="reason__text">From managed services to cybersecurity, we offer a comprehensive suite of IT solutions designed to meet the diverse needs of your business. Our holistic approach ensures that all aspects of your IT infrastructure are covered.</p>
  </div>

  <div class="page__foot foot--chip" role="img" aria-label="Glowing processor chip on a blue circuit board"></div>
  <div class="page__num">04</div>
</section>

<section class="page contact">
  <h2 class="contact__title">GET IN TOUCH</h2>
  <div class="contact__rule"></div>
  <p class="contact__lead">Discover how Korvalith can transform your IT landscape and drive your business forward. Contact us today to learn more about our services and how we can help you achieve your goals.</p>

  <div class="contact__label" style="top:344px">CONTACT US</div>
  <p class="contact__address">Unit 4 Harrow Mews, Fenwick Green, Northbridge, NB7 2QT</p>
  <div class="contact__row">
    <span class="contact__item"><span class="contact__icon"><svg width="14" height="14" viewBox="0 0 24 24" fill="none" stroke="#fff" stroke-width="1.6"><circle cx="12" cy="12" r="10"/><ellipse cx="12" cy="12" rx="4.5" ry="10"/><path d="M2 12h20"/></svg></span>www.korvalith.co.uk</span>
    <span class="contact__item"><span class="contact__icon"><svg width="13" height="13" viewBox="0 0 24 24" fill="none" stroke="#fff" stroke-width="1.8"><path d="M5 3h4l2 5-3 2a11 11 0 0 0 6 6l2-3 5 2v4a2 2 0 0 1-2 2A17 17 0 0 1 3 5a2 2 0 0 1 2-2z"/></svg></span>01632 960418</span>
    <span class="contact__item"><span class="contact__icon"><svg width="14" height="14" viewBox="0 0 24 24" fill="none" stroke="#fff" stroke-width="1.6"><rect x="3" y="5" width="18" height="14" rx="1"/><path d="M3 6l9 7 9-7"/></svg></span>info@korvalith.co.uk</span>
  </div>

  <div class="contact__label" style="top:455px">FOLLOW US</div>
  <p class="contact__follow">Stay updated with the latest news and updates from Korvalith</p>
  <div class="social" aria-label="Social media links">
    <span class="social__dot"></span><span class="social__dot"></span><span class="social__dot"></span>
  </div>
</section>

</body>
</html>
```